Roofing web site brvt roofing

Look at some of our competitors web page we like something similar with NYC roofing
https://www.quillbarroofing.example/
Maybe a skyline picture of nyc at the home page with a picture of flat roofing installation

Target Market(s)

Commercial and residential flat roofs

Industry/Entity Type

Flat Roofing industry

Coding

Coded - Design and coding required

Number of Pages Required

2 page

Font styles to use
Decorative
Script

Colors

Designer to choose colors to be used in the design.

Requirements
Must have
• At BRVT Roofing, we are a trusted and reputable roofing company specializing in new construction flat roof installation and repair. With years of experience in the industry, we take pride in providing exceptional roofing solutions to our valued clients. Our team of highly skilled and dedicated roofing professionals understands the unique challenges and requirements of new construction projects. We work closely with builders, contractors, and architects to design and install flat roofs that meet the specific needs of each project. From commercial buildings to residential complexes, we have the expertise to deliver reliable and durable roofing solutions. When it comes to flat roof repairs, we are your go-to experts. Our experienced technicians conduct thorough inspections to identify the root cause of any issues your roof may be experiencing. We utilize the latest industry techniques and high-quality materials to efficiently repair your flat roof, ensuring its integrity and longevity. At BRVT Roofing, we prioritize customer satisfaction above all else. We believe in building strong relationships with our clients by providing exceptional craftsmanship and outstanding customer service. Our team is dedicated to delivering projects on time, within budget, and to the highest standards of quality. We understand that a well-maintained roof is essential for protecting your property and ensuring the safety of its occupants. That's why we use only the best materials and employ skilled professionals who are trained in the latest roofing practices. Our commitment to excellence is evident in every project we undertake. As a fully licensed and insured roofing company, we prioritize safety and adhere to industry regulations and best practices. We take every precaution to create a safe working environment for our team and minimize any disruptions to your daily routine. When you choose BRVT Roofing, you can trust that you are working with a reliable and reputable company that will deliver exceptional results. We are committed to exceeding your expectations and providing you with a roof that is built to last. Contact us today for all your new construction flat roof installation and repair needs.
Nice to have
• NYC skyline background with commercial roofing pictures of torching roofing

```html
<!DOCTYPE html>
<html lang="en">
<head>
<meta charset="utf-8">
<title>BRVT Roofing</title>
<link href="https://fonts.googleapis.com/css2?family=Lora:wght@400;500&family=Roboto:wght@400;500;700&display=swap" rel="stylesheet">
<style>
:root{
  --orange:#f26b21;
  --orange-dark:#e05a12;
  --ink:#1d1d1d;
  --text:#666;
  --gray-bg:#f3f3f3;
  --footer:#0c0c0c;
  --white:#fff;
}
*{box-sizing:border-box;margin:0;padding:0}
html,body{width:1200px;height:4320px;overflow:hidden}
body{position:relative;font-family:'Roboto',sans-serif;color:var(--ink);background:var(--white)}
.abs{position:absolute}
.serif{font-family:'Lora',serif;font-weight:400}
.btn{position:absolute;display:flex;align-items:center;justify-content:center;gap:8px;background:var(--orange);color:#fff;font-weight:700;font-size:13px;text-transform:uppercase;border-radius:3px}
.btn .dot{width:13px;height:13px;border-radius:50%;background:#fff;display:inline-block;position:relative}
.btn .dot::after{content:"";position:absolute;left:4px;top:3.5px;border-left:5px solid var(--orange);border-top:3px solid transparent;border-bottom:3px solid transparent}
.photo{position:absolute}

/* header */
.header{position:absolute;left:0;top:0;width:1200px;height:97px;background:#fff}
.brand{left:144px;top:18px;font-family:'Lora',serif;font-size:30px;line-height:32px;color:#222}
.social-top{left:535px;top:17px;display:flex;gap:15px}
.social-top span{width:24px;height:24px;border-radius:50%;border:1.5px solid #f4b08a;display:block;position:relative}
.social-top span::after{content:"";position:absolute;left:7px;top:7px;width:7px;height:7px;border-radius:50%;background:var(--orange)}
.nav{left:377px;top:68px;display:flex;gap:0;font-size:13px;font-weight:500;text-transform:uppercase}
.nav a{color:#222;text-decoration:none;position:absolute;white-space:nowrap}
.call-box{right:0;top:0;width:316px;height:97px;background:var(--orange);clip-path:polygon(30px 0,100% 0,100% 100%,0 100%)}
.call-box .lbl{position:absolute;left:88px;top:28px;font-size:11px;color:#fff}
.call-box .num{position:absolute;left:88px;top:46px;font-size:20px;font-weight:500;color:#fff}
.call-box svg{position:absolute;left:42px;top:32px}

/* hero */
.hero{position:absolute;left:0;top:97px;width:1200px;height:600px;background:linear-gradient(180deg,#2b2b2e 0%,#3b3a38 45%,#7a6c5e 80%,#b9b2aa 100%)}
.hero-art{position:absolute;left:450px;top:210px;width:750px;height:360px;background:radial-gradient(ellipse at 60% 40%,rgba(210,160,80,.55),rgba(120,110,100,0) 65%)}
.hero .kicker{position:absolute;left:144px;top:84px;color:var(--orange);font-size:17px;font-weight:500}
.hero h1{position:absolute;left:143px;top:110px;color:#fff;font-size:52px}
.hero p{position:absolute;left:144px;top:198px;width:500px;color:#fff;font-size:15.5px;line-height:25px;font-weight:500}
.contact-band{position:absolute;left:0;top:630px;width:1200px;height:225px;background:var(--orange)}
.contact-item{position:absolute;top:726px;display:flex;gap:20px;color:#fff}
.contact-item .ico{width:73px;height:73px;background:#fff;border-radius:3px;display:flex;align-items:center;justify-content:center}
.contact-item h4{font-size:17px;font-weight:700;margin-top:2px}
.contact-item p{font-size:17px;line-height:26px}

/* about */
.about-photo{left:144px;top:934px;width:423px;height:389px;background:linear-gradient(160deg,#c7652f,#b0512a 55%,#7a5547)}
.about-card{left:354px;top:1273px;width:245px;height:87px;background:#a9a9a9;color:#fff;padding:16px 18px;font-size:14px;font-weight:500;line-height:22px}
.about-card b{font-size:15.5px;font-weight:500}
.about-txt{left:634px;top:950px;width:422px}
.kicker-sm{color:var(--orange);font-size:14px;font-weight:500;text-transform:uppercase}
.about-txt h2{font-size:40px;margin:6px 0 16px}
.about-txt p{font-size:13px;line-height:25px;color:var(--text);text-align:justify;margin-bottom:12px}
.mini-call{left:810px;top:1253px;display:flex;gap:12px;align-items:center}
.mini-call .lbl{font-size:11px;color:#555}
.mini-call .num{font-size:19px;font-weight:500;color:var(--orange)}

/* services */
.services{position:absolute;left:0;top:1459px;width:1200px;height:676px;background:var(--gray-bg)}
.center{position:absolute;left:0;width:1200px;text-align:center}
.svc{position:absolute;top:1638px;width:287px;height:413px;background:#fff;border-radius:8px;box-shadow:0 4px 14px rgba(0,0,0,.12);text-align:center}
.svc .img{position:absolute;left:7px;top:7px;width:273px;height:200px;border-radius:4px}
.svc h3{position:absolute;top:234px;width:100%;font-size:16px;font-weight:500}
.svc p{position:absolute;top:267px;left:10px;right:10px;font-size:13px;line-height:21px;color:var(--text)}
.svc .btn{left:72px;top:347px;width:143px;height:39px}
.arrow{position:absolute;top:1835px;width:26px;height:26px;border-radius:50%;display:flex;align-items:center;justify-content:center}

/* installs */
.installs{position:absolute;left:0;top:2135px;width:1200px;height:381px;background:linear-gradient(90deg,#ef6a22,#f37a35 50%,#ee6920)}
.inst-card{position:absolute;top:2365px;width:438px;height:285px;background:#fff;border-radius:4px;box-shadow:0 4px 18px rgba(0,0,0,.1);text-align:center}
.inst-card.active{border-bottom:4px solid var(--orange)}
.inst-card .circ{position:absolute;left:179px;top:32px;width:82px;height:82px;border-radius:50%;display:flex;align-items:center;justify-content:center}
.inst-card h3{position:absolute;top:133px;width:100%;font-size:17px;font-weight:500}
.inst-card p{position:absolute;top:166px;left:36px;right:36px;font-size:13px;line-height:21px;color:var(--text)}

/* gallery */
.gal{position:absolute}

/* subscribe */
.subscribe{position:absolute;left:0;top:3555px;width:1200px;height:333px;background:linear-gradient(90deg,#ee6620,#f3793a,#ee6620);clip-path:polygon(0 17px,50% 0,100% 17px,100% 100%,0 100%)}
.field{position:absolute;top:3726px;height:40px;background:#fff;border-radius:2px;font-size:13px;color:#888;display:flex;align-items:center;padding-left:14px;gap:7px}
.sub-btn{position:absolute;left:525px;top:3793px;width:149px;height:42px;background:#fff;color:var(--orange);font-size:13px;font-weight:700;display:flex;align-items:center;justify-content:center;border-radius:2px}

/* footer */
.footer{position:absolute;left:0;top:3888px;width:1200px;height:432px;background:var(--footer);color:#fff}
.f-brand{left:144px;top:3990px;font-family:'Lora',serif;font-size:34px;line-height:35px;color:#fff}
.f-social{left:163px;top:4094px;display:flex;gap:11px}
.f-social span{width:26px;height:26px;border-radius:50%;display:block}
.f-col{top:3962px;font-size:12.5px}
.f-col h4{font-size:15px;font-weight:700;margin-bottom:18px}
.f-col li{list-style:none;line-height:24px}
.f-contact{left:845px;top:3962px;width:230px;font-size:12px}
.f-contact h4{font-size:15px;font-weight:700;margin-bottom:14px}
.f-row{display:flex;gap:8px;margin-bottom:9px}
.f-row b{display:block;font-size:11px;font-weight:700;margin-bottom:3px}
.f-row div{line-height:17px}
.f-line{left:144px;top:4259px;width:912px;height:1px;background:#2a2a2a}
.copy{top:4280px;font-size:12px;color:#fff}
.to-top{left:1072px;top:4234px;width:34px;height:34px;border-radius:50%;background:var(--orange);display:flex;align-items:center;justify-content:center}
</style>
</head>
<body>

<!-- Header -->
<header class="header">
  <div class="abs brand">BRVT<br>Roofing</div>
  <div class="abs social-top"><span></span><span></span><span></span><span></span></div>
  <a class="btn" style="left:704px;top:13px;width:143px;height:36px;font-size:12px">Get a Quote <i class="dot"></i></a>
  <nav class="abs nav">
    <a style="left:0;color:var(--orange)">Home</a>
    <a style="left:76px">About Us</a>
    <a style="left:184px">Services</a>
    <a style="left:285px">Gallery</a>
    <a style="left:382px">Contact Us</a>
  </nav>
  <div class="abs call-box">
    <svg width="34" height="34" viewBox="0 0 34 34"><circle cx="17" cy="17" r="16" fill="#fff"/><path d="M11 10c1-1 2.5-1 3 0l1.5 3c.4 1-.2 1.6-1 2.2 1 2 2.6 3.7 4.5 4.6.6-.8 1.3-1.4 2.2-1l3 1.5c1 .5 1 2 0 3l-1.2 1.2c-4 1.5-13-7.5-12.5-12.5z" fill="var(--orange)"/></svg>
    <div class="lbl">Call Us Today</div>
    <div class="num">555-010-4821</div>
  </div>
</header>

<!-- Hero -->
<section class="hero">
  <div class="hero-art" role="img" aria-label="City skyline at dusk with a roofer rolling out a membrane on a flat roof"></div>
  <div class="kicker">Welcome To</div>
  <h1 class="serif">BRVT Roofing</h1>
  <p>Professional &amp; Affordable Roofing Services. Call Today For a Free Quote! Storm damage, roof installation, roof repairs.</p>
  <a class="btn" style="left:144px;top:272px;width:166px;height:47px;font-size:14px">Book Now <i class="dot"></i></a>
</section>

<svg class="abs" style="left:0;top:630px" width="1200" height="60" viewBox="0 0 1200 60" preserveAspectRatio="none">
  <path d="M0 20 C150 0 300 45 450 30 C560 18 640 -4 760 20 C900 46 1050 0 1200 22 L1200 60 L0 60Z" fill="var(--orange)"/>
</svg>
<div class="contact-band" style="top:670px;height:185px"></div>

<div class="contact-item" style="left:144px">
  <div class="ico"><svg width="40" height="44" viewBox="0 0 40 44" fill="none" stroke="var(--orange)" stroke-width="2"><path d="M20 32s-10-10-10-17a10 10 0 0 1 20 0c0 7-10 17-10 17z"/><circle cx="20" cy="15" r="4"/><path d="M8 34l-5 8h34l-5-8"/></svg></div>
  <div><h4>LOCATION:</h4><p>Lorem ipsum dolor sit amet,<br>adipiscing elit 6809</p></div>
</div>
<div class="contact-item" style="left:539px;top:726px">
  <div class="ico"><svg width="40" height="40" viewBox="0 0 40 40" fill="none" stroke="var(--orange)" stroke-width="2"><path d="M9 6c2-2 4-2 5 0l3 5c1 2 0 3-2 4 2 4 5 7 9 9 1-2 2-3 4-2l5 3c2 1 2 3 0 5l-3 3C22 34 4 17 9 6z"/><path d="M24 8a9 9 0 0 1 8 8M24 3a14 14 0 0 1 13 13"/></svg></div>
  <div style="padding-top:10px"><h4>PHONE:</h4><p>555-010-4821</p></div>
</div>
<div class="contact-item" style="left:838px;top:726px">
  <div class="ico"><svg width="44" height="34" viewBox="0 0 44 34" fill="none" stroke="var(--orange)" stroke-width="2"><rect x="2" y="2" width="40" height="30"/><path d="M2 2l20 17L42 2M2 32l15-14M42 32L27 18"/></svg></div>
  <div style="padding-top:10px"><h4>EMAIL:</h4><p>info@brvtroofing.example</p></div>
</div>

<!-- About -->
<div class="photo about-photo" role="img" aria-label="Worker pressure-washing a terracotta tile roof beside a skylight"></div>
<div class="abs about-card"><b>Have a Roof Repair?</b><br>Contact Our Friendly Team!</div>
<a class="btn" style="left:379px;top:1342px;width:194px;height:38px;font-size:12px">Schedule a Service <i class="dot"></i></a>
<div class="abs about-txt">
  <div class="kicker-sm">About Us</div>
  <h2 class="serif">BRVT Roofing</h2>
  <p>At BRVT Roofing, we are a trusted and reputable roofing company specializing in new construction flat roof installation and repair. With years of experience in the industry, we take pride in providing exceptional roofing solutions to our valued clients.</p>
  <p>Our team of highly skilled and dedicated roofing professionals understands the unique challenges and requirements of new construction projects, We work closely with builders, contractors.</p>
</div>
<a class="btn" style="left:634px;top:1254px;width:138px;height:42px">Read More <i class="dot"></i></a>
<div class="abs mini-call">
  <svg width="38" height="38" viewBox="0 0 34 34"><circle cx="17" cy="17" r="16" fill="var(--orange)"/><path d="M11 10c1-1 2.5-1 3 0l1.5 3c.4 1-.2 1.6-1 2.2 1 2 2.6 3.7 4.5 4.6.6-.8 1.3-1.4 2.2-1l3 1.5c1 .5 1 2 0 3l-1.2 1.2c-4 1.5-13-7.5-12.5-12.5z" fill="#fff"/></svg>
  <div><div class="lbl">Call Us Today</div><div class="num">555-010-4821</div></div>
</div>

<!-- Services -->
<section class="services"></section>
<div class="center kicker-sm" style="top:1527px;font-size:13px">We're Here When You Need Us</div>
<h2 class="center serif" style="top:1555px;font-size:44px">Our Services</h2>

<div class="arrow" style="left:52px;background:#888"><svg width="10" height="10" viewBox="0 0 10 10"><path d="M7 1L3 5l4 4" stroke="#fff" stroke-width="2" fill="none"/></svg></div>
<div class="arrow" style="left:1122px;background:var(--orange)"><svg width="10" height="10" viewBox="0 0 10 10"><path d="M3 1l4 4-4 4" stroke="#fff" stroke-width="2" fill="none"/></svg></div>

<div class="svc" style="left:144px">
  <div class="img" role="img" aria-label="Roofer in a hard hat working on a roof at sunset" style="background:linear-gradient(160deg,#6f8fb3,#b8a27a 60%,#5a4a3a)"></div>
  <h3>Reliable Roofing Professionals</h3>
  <p>As specialists in residential and commercial roofing services, we are dedicated to providing customer service</p>
  <a class="btn">Read More <i class="dot"></i></a>
</div>
<div class="svc" style="left:456px">
  <div class="img" role="img" aria-label="Two workers installing solar panels on a dark metal roof" style="background:linear-gradient(170deg,#a9c3dc,#5f6f7e 45%,#2f3a44)"></div>
  <h3>Individualized Roofing Options</h3>
  <p>We provide a full consultation to explain your available options so that you can choose the roofing plan</p>
  <a class="btn">Read More <i class="dot"></i></a>
</div>
<div class="svc" style="left:768px">
  <div class="img" role="img" aria-label="Inspector with a clipboard beside a house gable" style="background:linear-gradient(160deg,#cfd8e2,#9aa6b2 50%,#c4825a)"></div>
  <h3>Satisfaction Guaranteed</h3>
  <p>We strive to save you both time and money by combining roofing knowledge, the highest quality parts and equipment,</p>
  <a class="btn">Read More <i class="dot"></i></a>
</div>

<!-- Perfect Installs -->
<section class="installs" role="img" aria-label="Orange-tinted photo of roofers at work"></section>
<h2 class="center serif" style="top:2183px;font-size:42px;color:#fff">Perfect Installs</h2>
<p class="center" style="top:2264px;font-size:17px;line-height:29px;color:#fff;font-weight:500">Your roof is your main defense against the elements. Let us walk you through the best options to fit your needs and<br>once you feel comfortable with your choice, we'll handle the complete installation.</p>

<div class="inst-card active" style="left:144px">
  <div class="circ" style="background:var(--orange);box-shadow:0 0 0 4px #fde4d4">
    <svg width="44" height="40" viewBox="0 0 44 40" fill="none" stroke="#fff" stroke-width="2"><path d="M4 20l8-8 8 4 6-4 14 8M10 26l6 6 4-2 4 4 4-2 6-6M22 6v6M16 4l2 5M28 4l-2 5"/></svg>
  </div>
  <h3>Reliable Upgrades</h3>
  <p>Lorem ipsum dolor sit amet, consectetur adipiscing elit, sed do eiusmod tempor incididunt ut labore et dolore magna aliqua, Ut enim ad minim veniam, quis nostrud exercitation ullamco laboris nisi ut aliquip ex ea commodo consequat.</p>
</div>
<div class="inst-card" style="left:617px">
  <div class="circ" style="background:#fff;box-shadow:0 2px 10px rgba(0,0,0,.12)">
    <svg width="44" height="44" viewBox="0 0 44 44" fill="none" stroke="#333" stroke-width="2"><path d="M14 14a8 8 0 0 1 16 0zM12 14h20M22 6v4"/><circle cx="22" cy="20" r="5"/><circle cx="12" cy="32" r="5"/><path d="M26 28l10 10M34 26l-8 10"/></svg>
  </div>
  <h3>Upkeep &amp; Repair</h3>
  <p>Lorem ipsum dolor sit amet, consectetur adipiscing elit, sed do eiusmod tempor incididunt ut labore et dolore magna aliqua, Ut enim ad minim veniam, quis nostrud exercitation ullamco laboris nisi ut aliquip ex ea commodo consequat.</p>
</div>
<a class="btn" style="left:516px;top:2695px;width:167px;height:39px">Find Out More <i class="dot"></i></a>

<!-- Gallery -->
<h2 class="center serif" style="top:2796px;font-size:44px">Our Gallery</h2>
<div class="gal" role="img" aria-label="Roofer in work trousers unrolling roofing membrane" style="left:144px;top:2894px;width:451px;height:262px;background:linear-gradient(160deg,#e9eef0,#8aa193 45%,#5b6a60)"></div>
<div class="gal" role="img" aria-label="Worker applying white coating to a flat roof with a roller" style="left:604px;top:2894px;width:452px;height:262px;background:linear-gradient(160deg,#cfd4d8,#e5e7e8 50%,#7b8288)"></div>
<div class="gal" role="img" aria-label="Hands using a nail gun on asphalt shingles" style="left:148px;top:3166px;width:300px;height:235px;background:linear-gradient(160deg,#b09070,#d0a040 45%,#7f8a90)"></div>
<div class="gal" role="img" aria-label="Gloved hands fitting shingles" style="left:458px;top:3166px;width:288px;height:235px;background:linear-gradient(160deg,#6e6a68,#d78a52 50%,#9fa3a6)"></div>
<div class="gal" role="img" aria-label="Worker laying a sheet on a roof edge" style="left:756px;top:3166px;width:300px;height:235px;background:linear-gradient(160deg,#9ab0a8,#c6483d 45%,#dde3e1)"></div>
<svg class="abs" style="left:581px;top:3436px" width="38" height="14" viewBox="0 0 38 14"><circle cx="6" cy="7" r="5" fill="#aaa"/><circle cx="19" cy="7" r="5" fill="none" stroke="var(--orange)" stroke-width="2"/><circle cx="19" cy="7" r="2.5" fill="var(--orange)"/><circle cx="32" cy="7" r="5" fill="#aaa"/></svg>

<!-- Subscribe -->
<section class="subscribe"></section>
<h2 class="center serif" style="top:3608px;font-size:40px;color:#fff">Flat Roof Installation Roof Repair</h2>
<p class="center" style="top:3680px;font-size:13px;color:#fde0cd">Sign up to receive maintenance reminders and hear about our latest projects.</p>
<div class="field" style="left:221px;width:364px"><svg width="11" height="11" viewBox="0 0 11 11"><circle cx="5.5" cy="3" r="2.8" fill="#888"/><path d="M0 11c0-4 11-4 11 0z" fill="#888"/></svg>Your Name</div>
<div class="field" style="left:614px;width:364px"><svg width="12" height="9" viewBox="0 0 12 9"><rect width="12" height="9" fill="#888"/><path d="M0 0l6 5 6-5" stroke="#fff" fill="none"/></svg>Email Address</div>
<div class="sub-btn">SUBSCRIBE</div>

<!-- Footer -->
<footer class="footer"></footer>
<div class="abs f-brand">BRVT<br>Roofing</div>
<div class="abs f-social">
  <span style="background:#1f4fa8"></span><span style="background:#1a6fb5"></span><span style="background:#d32323"></span><span style="background:#a23fb0"></span>
</div>
<div class="abs f-col" style="left:421px"><h4>Quick Links</h4><ul><li>Home</li><li>About Us</li><li>Services</li><li>Our Gallery</li><li>Contact Us</li></ul></div>
<div class="abs f-col" style="left:612px"><h4>About Company</h4><ul><li>Terms of Use</li><li>Terms &amp; Condition</li><li>News</li><li>Contact Us</li><li>FAQ</li></ul></div>
<div class="abs f-contact">
  <h4>Contact Us</h4>
  <div class="f-row"><svg width="12" height="14" viewBox="0 0 12 14"><path d="M6 14S0 8 0 5a6 6 0 0 1 12 0c0 3-6 9-6 9z" fill="var(--orange)"/><circle cx="6" cy="5" r="2" fill="#000"/></svg><div><b>Location</b>6809, Lorem ipsum dolor sit amet, consectetur adipiscing elit,</div></div>
  <div class="f-row"><svg width="12" height="12" viewBox="0 0 12 12"><path d="M2 1c1-1 2-1 2.5 0l1 2c.3.7-.1 1.1-.7 1.5.7 1.4 1.8 2.5 3.2 3.2.4-.6.8-1 1.5-.7l2 1c1 .5 1 1.5 0 2.5C9 12 0 5 2 1z" fill="var(--orange)"/></svg><div><b>Phone</b>555-010-4821</div></div>
  <div class="f-row"><svg width="12" height="10" viewBox="0 0 12 10"><rect width="12" height="10" fill="var(--orange)"/><path d="M0 0l6 5 6-5" stroke="#000" fill="none"/></svg><div><b>Email</b>info@brvtroofing.example</div></div>
  <div class="f-row"><svg width="12" height="12" viewBox="0 0 12 12"><rect width="12" height="12" rx="2" fill="var(--orange)"/><path d="M3 6h6M3 3h6M3 9h4" stroke="#000"/></svg><div><b>Hours</b>Monday - Friday: 8am - 5pm<br>Saturday - Sunday: 8am-12</div></div>
</div>
<div class="abs f-line"></div>
<div class="abs to-top"><svg width="12" height="10" viewBox="0 0 12 10"><path d="M1 8l5-5 5 5" stroke="#fff" stroke-width="2" fill="none"/></svg></div>
<div class="center copy">Copyright © 2024 BRVT Construction Roofing - All Rights Reserved.</div>

</body>
</html>
```